Make a CV more classy for an orthopaedic hand surgeon

I actually don't want a resume with many pictures etc. I want a CV that is classy, and would be attractive to lawyers. I want you to keep the same content in my current CV just rearrange things if necessary and make it nice, with nice headers and organization. Again, like the sleek, classy, luxury, but professional look. I want lawyers and other recruiters to look at my CV and know I am high class

Target Market(s)

Lawyers, Consulting gigs--they want to see that I am smart and have a lot of accolades

Industry/Entity Type

Medicine

Colors
0054AA
0677BA
7BADD7
CADEEF
E8F1F8

Requirements
Must have
• Classy, luxury, professional
Nice to have
• NA
Should not have
• Additional photos, resume-type look--bubbles everywhere, boxes circled. Should look like the format it is in already, just spiced up and organized better with nice fancy headers and sleek look

```html
<!DOCTYPE html>
<html lang="en">
<head>
<meta charset="utf-8">
<title>Helena Marsh, M.D. — Curriculum Vitae</title>
<link href="https://fonts.googleapis.com/css2?family=Montserrat:wght@300;400;500;600;700&display=swap" rel="stylesheet">
<style>
:root{
  --backdrop:#9b9b9b;
  --paper:#ffffff;
  --ink:#151515;
  --muted:#6f6f6f;
  --rule:#c9c9c9;
  --gold-light:#e2c889;
  --gold-dark:#c6a14f;
}
*{box-sizing:border-box;margin:0;padding:0}
html,body{width:1200px;height:1200px;overflow:hidden}
body{background:var(--backdrop);font-family:'Montserrat',sans-serif;color:var(--ink);position:relative}
.cv-page{position:absolute;left:175px;top:50px;width:850px;height:1100px;background:var(--paper);overflow:hidden}
.cv-header{position:absolute;left:60px;top:70px;right:60px}
.cv-name{font-size:40px;font-weight:700;letter-spacing:1px;line-height:1}
.cv-title{margin-top:12px;font-size:15px;font-weight:600;letter-spacing:2.2px}
.brand-mark{position:absolute;right:0;top:-22px;display:flex;align-items:center;gap:10px}
.brand-mark .brand-circle{width:54px;height:54px;border:3px solid var(--ink);border-radius:50%}
.brand-mark .brand-name{font-size:15px;font-weight:700;letter-spacing:2px}
.contact-bar{position:absolute;left:60px;right:60px;top:160px;border-top:1px solid var(--rule);border-bottom:1px solid var(--rule);padding:16px 0;display:flex;align-items:center;font-size:10.5px;color:var(--muted);font-weight:300}
.contact-item{padding:0 22px;border-left:1px solid var(--rule);line-height:1.45}
.contact-item:first-child{padding-left:0;border-left:none}
.contact-label{font-weight:600;color:var(--ink);letter-spacing:1px;margin-right:6px}
.cv-sections{position:absolute;left:60px;right:50px;top:260px}
.cv-section{display:grid;grid-template-columns:230px 1fr;margin-bottom:44px}
.section-heading{font-size:14px;font-weight:700;letter-spacing:1.5px;line-height:1.15;text-transform:uppercase}
.timeline{position:relative;padding-left:20px}
.timeline::before{content:"";position:absolute;left:3px;top:6px;bottom:6px;width:1px;background:var(--rule)}
.timeline.row{display:flex;gap:40px;padding-left:0}
.timeline.row::before{display:none}
.entry{position:relative;margin-bottom:14px;font-size:11px;line-height:1.45}
.timeline.row .entry{padding-left:20px}
.entry::before{content:"";position:absolute;left:-20px;top:4px;width:7px;height:7px;border-radius:50%;background:var(--ink)}
.timeline.row .entry::before{left:0}
.entry-date{font-weight:600;font-size:12px}
.entry-role{font-weight:600}
.entry-place{color:var(--muted);font-weight:300;font-style:italic}
.entry-plain{color:var(--muted);font-weight:400}
.member{display:grid;grid-template-columns:40px 18px 1fr;margin-bottom:9px;font-size:11px;line-height:1.4}
.member .year{font-weight:600}
.member .dash{color:var(--muted)}
.member .org{color:#3a3a3a}
.gold-band{position:absolute;left:0;right:0;bottom:0;height:26px;background:linear-gradient(90deg,var(--gold-light),var(--gold-dark))}
</style>
</head>
<body>
<main class="cv-page">
  <header class="cv-header">
    <h1 class="cv-name">HELENA MARSH, M.D.</h1>
    <p class="cv-title">BOARD CERTIFIED, HAND SUBSPECIALTY CERTIFIED</p>
    <div class="brand-mark"><span class="brand-circle"></span><span class="brand-name">HM HAND</span></div>
  </header>

  <div class="contact-bar">
    <div class="contact-item">4120 Harbor View Lane, Suite 305<br>Linden Park, FL 33099</div>
    <div class="contact-item"><span class="contact-label">PHONE:</span>555-014-2210</div>
    <div class="contact-item"><span class="contact-label">FAX:</span>555-014-2231</div>
    <div class="contact-item"><span class="contact-label">CELL:</span>555-019-4482</div>
  </div>

  <div class="cv-sections">
    <section class="cv-section">
      <h2 class="section-heading">Education:</h2>
      <div class="timeline row">
        <div class="entry"><div class="entry-date">Aug/2005 - May/2009</div><div class="entry-plain">BS - Whitmore University</div></div>
        <div class="entry"><div class="entry-date">Aug/2009 - May/2013</div><div class="entry-plain">MD - Crestview School of<br>Medicine and Dentistry</div></div>
      </div>
    </section>

    <section class="cv-section">
      <h2 class="section-heading">Post-Graduate<br>Training &amp;<br>Fellowship<br>Appointments:</h2>
      <div class="timeline">
        <div class="entry"><div class="entry-date">Jun/2013 - Jul/2018</div><div class="entry-role">Resident in Orthopaedic Surgery</div><div class="entry-place">Harborview General Hospital, Newbury</div></div>
        <div class="entry"><div class="entry-date">Aug/2018 - Jul/2019</div><div class="entry-role">Fellow in Hand Surgery</div><div class="entry-place">Hospital of Eastbrook University, Eastbrook</div></div>
      </div>
    </section>

    <section class="cv-section">
      <h2 class="section-heading">Employment<br>History:</h2>
      <div class="timeline">
        <div class="entry"><div class="entry-date">Sep/2019 - Sep/2021</div><div class="entry-role">Hand &amp; Upper Extremity Orthopaedic Surgeon, Southfield Medical Partners</div><div class="entry-place">Group, Marietta GA</div></div>
        <div class="entry"><div class="entry-date">Oct/2021 - Present</div><div class="entry-role">Hand &amp; Upper Extremity Orthopaedic Surgeon, Owner, HM Hand &amp; Upper</div><div class="entry-place">Extremity Surgery PLLC</div></div>
      </div>
    </section>

    <section class="cv-section">
      <h2 class="section-heading">Board<br>Certification:</h2>
      <div class="timeline">
        <div class="entry"><div class="entry-date">Nov/2021 - Present</div><div class="entry-plain">National Board of Orthopaedic Surgery (NBOS),<br>Certified in Orthopaedic Surgery</div></div>
        <div class="entry"><div class="entry-date">Aug/2022</div><div class="entry-plain">NBOS, Certified in Surgery of the Hand</div></div>
      </div>
    </section>

    <section class="cv-section">
      <h2 class="section-heading">Memberships in<br>Professional and<br>Scientific Societies:</h2>
      <div class="members">
        <div class="member"><span class="year">2019</span><span class="dash">—</span><span class="org">NSHS Member</span></div>
        <div class="member"><span class="year">2016</span><span class="dash">—</span><span class="org">NSHS Resident Candidate Member</span></div>
        <div class="member"><span class="year">2015</span><span class="dash">—</span><span class="org">Resident member, OrthoTrauma Forum</span></div>
        <div class="member"><span class="year">2013</span><span class="dash">—</span><span class="org">Resident Member, Harborview General Hospital Minority Housestaff Organization</span></div>
        <div class="member"><span class="year">2013</span><span class="dash">—</span><span class="org">Resident Member, National Academy of Orthopaedic Surgeons</span></div>
        <div class="member"><span class="year">2009</span><span class="dash">—</span><span class="org">National Student Medical Alliance (NSMA)</span></div>
      </div>
    </section>
  </div>

  <div class="gold-band"></div>
</main>
</body>
</html>
```